KBT Business Cards

We require business cards for our business. We would like a matte black back to the card, with our logo centred in the middle. The front side of the card is open to design.

Target Market(s)

Clients looking for legal services (professional)

Industry/Entity Type

Legal

Contact Information for Business Card

Doran Kelbrath
Partner
Mobile: 0461 738 524
Email: doran@kbtlaw.co
Website: www.kbtlaw.co
Level 3, 118 Wendmore Street
Sydney NSW 2000

Font styles to use
Other font styles liked:
• Avenir

Colors
f04a50
ffffff
1b1b1b

Requirements
Must have
• Black back with logo included in the centre of the card.
• Our font is Avenir.

```html
<!DOCTYPE html>
<html lang="en">
<head>
<meta charset="utf-8">
<title>KBT Legal Business Cards</title>
<link rel="stylesheet" href="https://fonts.googleapis.com/css2?family=Nunito+Sans:wght@400;700;800&display=swap">
<style>
  :root {
    --brand-red: #d01f45;
    --brand-red-deep: #b5173a;
    --ink: #1b1b1b;
    --paper: #ffffff;
    --stage: #262626;
    --text-font: "Nunito Sans", "Avenir", sans-serif;
  }
  * { box-sizing: border-box; margin: 0; padding: 0; }
  html, body {
    width: 1200px; height: 960px; overflow: hidden;
    background: var(--stage);
    font-family: var(--text-font);
  }
  .sheet {
    width: 1200px; height: 960px;
    display: flex; flex-direction: column;
    align-items: center; justify-content: center;
    gap: 60px;
  }
  .card {
    position: relative;
    width: 640px; height: 391px;
    overflow: hidden;
    box-shadow: 0 12px 30px rgba(0,0,0,0.45);
  }
  /* Back */
  .card--back {
    background: var(--ink);
    display: flex; align-items: center; justify-content: center;
  }
  .wordmark {
    display: flex; align-items: center; gap: 14px;
    font-weight: 800; text-transform: uppercase;
    letter-spacing: 0.02em; line-height: 1;
  }
  .wordmark__square { display: block; background: var(--brand-red); }
  .card--back .wordmark { font-size: 46px; color: var(--paper); }
  .card--back .wordmark__square { width: 34px; height: 34px; }

  /* Front */
  .card--front { background: var(--paper); }
  .front-shapes { position: absolute; inset: 0; }
  .card--front .wordmark {
    position: absolute; left: 40px; top: 62px;
    font-size: 40px; color: var(--ink);
  }
  .card--front .wordmark__square { width: 30px; height: 30px; }

  .holder {
    position: absolute; left: 40px; top: 184px;
    color: var(--paper);
  }
  .holder__name {
    font-size: 21px; font-weight: 800; text-transform: uppercase;
    letter-spacing: 0.03em; line-height: 1.1;
  }
  .holder__role {
    font-size: 13px; font-weight: 400; text-transform: uppercase;
    letter-spacing: 0.06em; margin-top: 2px;
  }
  .holder__contacts { list-style: none; margin-top: 10px; }
  .holder__contacts li {
    display: flex; align-items: center; gap: 8px;
    font-size: 14px; line-height: 1.55; white-space: nowrap;
  }
  .icon { width: 13px; height: 13px; flex: none; }

  .office {
    position: absolute; right: 34px; bottom: 26px;
    text-align: right; color: var(--paper);
    font-size: 15px; line-height: 1.45; font-style: normal;
    white-space: nowrap;
  }
  .office__web {
    display: flex; align-items: center; justify-content: flex-end;
    gap: 8px; margin-top: 8px;
  }
</style>
</head>
<body>
<main class="sheet">

  <section class="card card--back" aria-label="Card back">
    <div class="wordmark">
      <span class="wordmark__square"></span>
      <span class="wordmark__name">KBT Legal</span>
    </div>
  </section>

  <section class="card card--front" aria-label="Card front">
    <svg class="front-shapes" viewBox="0 0 640 391" aria-hidden="true">
      <defs>
        <linearGradient id="redBand" x1="0" y1="0" x2="1" y2="0">
          <stop offset="0" stop-color="var(--brand-red-deep)"/>
          <stop offset="1" stop-color="var(--brand-red)"/>
        </linearGradient>
      </defs>
      <polygon class="band band--upper" fill="url(#redBand)"
        points="0,172 420,172 396,206 280,206 190,330 0,330"/>
      <polygon class="band band--lower" fill="url(#redBand)"
        points="0,344 200,344 290,220 340,220 400,391 0,391"/>
      <polygon class="panel panel--dark" fill="var(--ink)"
        points="352,220 640,220 640,391 414,391"/>
    </svg>

    <div class="wordmark">
      <span class="wordmark__square"></span>
      <span class="wordmark__name">KBT Legal</span>
    </div>

    <div class="holder">
      <p class="holder__name">Doran Kelbrath</p>
      <p class="holder__role">Partner</p>
      <ul class="holder__contacts">
        <li>
          <svg class="icon" viewBox="0 0 14 14" aria-hidden="true">
            <rect x="3" y="0.8" width="8" height="12.4" rx="1.6" fill="none" stroke="#fff" stroke-width="1.4"/>
            <circle cx="7" cy="10.6" r="0.9" fill="#fff"/>
          </svg>
          <span>0461 738 524</span>
        </li>
        <li>
          <svg class="icon" viewBox="0 0 14 14" aria-hidden="true">
            <rect x="0.8" y="2.5" width="12.4" height="9" fill="none" stroke="#fff" stroke-width="1.4"/>
            <polyline points="1,3 7,8 13,3" fill="none" stroke="#fff" stroke-width="1.4"/>
          </svg>
          <span>doran@kbtlaw.co</span>
        </li>
      </ul>
    </div>

    <address class="office">
      <p>Level 3, 118 Wendmore Street</p>
      <p>Sydney NSW 2000</p>
      <p class="office__web">
        <span>www.kbtlaw.co</span>
        <svg class="icon" viewBox="0 0 14 14" aria-hidden="true">
          <circle cx="7" cy="7" r="6" fill="none" stroke="#fff" stroke-width="1.2"/>
          <ellipse cx="7" cy="7" rx="2.6" ry="6" fill="none" stroke="#fff" stroke-width="1.1"/>
          <line x1="1" y1="7" x2="13" y2="7" stroke="#fff" stroke-width="1.1"/>
        </svg>
      </p>
    </address>
  </section>

</main>
</body>
</html>
```